Income Tax Business Cards - Updates

Need to update these business cards while keeping all the same wording but just update them and make them look nicer and more modern/ on brand with our brand.

Industry/Entity Type

finance

Contact Information for Business Card

we have multiple locations so will just need to easily be able to change the address and phone numbers

Colors

Designer to choose colors to be used in the design.

```html
<!DOCTYPE html>
<html lang="en">
<head>
<meta charset="utf-8">
<title>Ledgerline Financial Group – Business Cards</title>
<link rel="stylesheet" href="https://fonts.googleapis.com/css2?family=Open+Sans:wght@400;600;700;800&display=swap">
<style>
  :root {
    --green: #0f4d2c;
    --red: #c41e24;
    --white: #ffffff;
    --ink: #1d1d1d;
    --bg: #2b2b2b;
    --rule: #8aa596;
  }
  * { box-sizing: border-box; margin: 0; padding: 0; }
  html, body { width: 1200px; height: 875px; overflow: hidden; }
  body {
    background: var(--bg);
    font-family: "Open Sans", Arial, sans-serif;
    position: relative;
  }
  .card {
    position: absolute;
    width: 540px;
    height: 310px;
    border-radius: 26px;
    overflow: hidden;
    box-shadow: 0 18px 40px rgba(0,0,0,.45);
  }
  /* Back card */
  .card-back {
    left: 40px; top: 150px;
    background: var(--green);
    color: var(--white);
    display: flex; flex-direction: column;
    align-items: center; justify-content: center;
    text-align: center;
  }
  .brand {
    display: flex; align-items: center; gap: 12px;
    font-weight: 700;
  }
  .brand-dot { width: 16px; height: 16px; border-radius: 50%; background: var(--red); flex: none; }
  .card-back .brand { font-size: 34px; color: var(--white); letter-spacing: .5px; }
  .brand-sub { font-weight: 700; font-size: 34px; }
  .back-tagline {
    margin-top: 40px;
    font-weight: 800; font-size: 22px; line-height: 1.2; text-transform: uppercase;
  }
  .back-tagline small { display: block; font-size: 17px; }

  /* Front card */
  .card-front {
    left: 620px; top: 400px;
    background: var(--white);
  }
  .front-bands { position: absolute; inset: 0; }
  .front-logo {
    position: absolute; left: 34px; top: 100px; width: 240px;
  }
  .card-front .brand { font-size: 26px; color: var(--green); line-height: 1.15; }
  .divider {
    position: absolute; left: 300px; top: 40px; width: 1px; height: 150px; background: var(--rule);
  }
  .contact { position: absolute; left: 318px; top: 34px; color: var(--ink); }
  .contact-name { font-weight: 800; font-size: 21px; color: var(--green); text-transform: uppercase; }
  .contact-title { font-weight: 600; font-size: 14px; color: var(--red); margin-bottom: 10px; }
  .contact-list { list-style: none; font-size: 11.5px; line-height: 1.45; }
  .contact-list li { display: flex; gap: 7px; align-items: flex-start; margin-bottom: 3px; }
  .contact-list svg { width: 11px; height: 11px; margin-top: 3px; flex: none; fill: var(--red); }
  .estimates {
    position: absolute; left: 60px; top: 247px;
    color: var(--white); font-weight: 800; font-size: 22px; text-transform: uppercase; letter-spacing: .5px;
  }
  .advance {
    position: absolute; right: 22px; top: 222px; width: 160px;
    color: var(--white); text-align: center; text-transform: uppercase; line-height: 1.1;
  }
  .advance-amount { font-weight: 800; font-size: 21px; }
  .advance-line { font-weight: 800; font-size: 13px; }
  .advance-note { font-weight: 700; font-size: 7.5px; margin-top: 3px; letter-spacing: .3px; }
</style>
</head>
<body>

<section class="card card-back" aria-label="Business card back">
  <div class="brand"><span class="brand-dot"></span>Ledgerline</div>
  <div class="brand brand-sub">Financial Group</div>
  <p class="back-tagline">File your taxes here<small>Up to $6,000 same day advance</small></p>
</section>

<section class="card card-front" aria-label="Business card front">
  <svg class="front-bands" viewBox="0 0 540 310" preserveAspectRatio="none" aria-hidden="true">
    <path d="M0 238 L338 238 Q352 238 350 226 L350 226 L358 220 L358 300 L0 300 Z" fill="var(--red)"/>
    <path d="M0 294 L330 294 Q352 294 356 268 L362 232 Q366 206 392 206 L540 206 L540 310 L0 310 Z" fill="var(--green)"/>
    <path d="M0 284 L326 284 Q346 284 350 262 L356 228 Q361 198 392 198 L540 198 L540 206 L392 206 Q366 206 362 232 L356 268 Q352 294 330 294 L0 294 Z" fill="var(--white)"/>
  </svg>

  <div class="front-logo">
    <div class="brand"><span class="brand-dot"></span>Ledgerline</div>
    <div class="brand">Financial Group</div>
  </div>

  <div class="divider"></div>

  <div class="contact">
    <h1 class="contact-name">Daniel Reyes</h1>
    <p class="contact-title">Founder &amp; CEO</p>
    <ul class="contact-list">
      <li><svg viewBox="0 0 12 12"><path d="M6 0a4 4 0 0 0-4 4c0 3 4 8 4 8s4-5 4-8a4 4 0 0 0-4-4zm0 5.5A1.5 1.5 0 1 1 6 2.5a1.5 1.5 0 0 1 0 3z"/></svg><span>Your Address, City<br>State, Country, Zip 1235</span></li>
      <li><svg viewBox="0 0 12 12"><path d="M2.5 0.5l2 2-1 1.5c.6 1.5 2 2.9 3.5 3.5l1.5-1 2 2-1.5 2C5 10 2 7 0.5 2z"/></svg><span>(123) 456-7890</span></li>
      <li><svg viewBox="0 0 12 12"><path d="M0 2h12v8H0zM1 3l5 3.5L11 3"/></svg><span>office@ledgerline.com</span></li>
      <li><svg viewBox="0 0 12 12"><path d="M6 0a6 6 0 1 0 0 12A6 6 0 0 0 6 0zm0 1.2c.8.9 1.3 2.4 1.4 4.2H4.6C4.7 3.6 5.2 2.1 6 1.2zM4.6 6.6h2.8C7.3 8.4 6.8 9.9 6 10.8c-.8-.9-1.3-2.4-1.4-4.2z"/></svg><span>www.ledgerline.com</span></li>
    </ul>
  </div>

  <p class="estimates">Free Estimates!</p>

  <div class="advance">
    <p class="advance-amount">Up to $6,000</p>
    <p class="advance-line">Same day advance</p>
    <p class="advance-note">— On approved tax returns! —</p>
  </div>
</section>

</body>
</html>
```